Business card for my new company (Accounting firm)

I need a business card for my new business Brightwell Advisory and Ledger SA. Our services are accounting, tax, audit and financial management. Our customers are small companies, start-ups and new companies. The final design has to show financial security, trust and growth. Please find our logo attached to the business card. Text for the business card: Brightwell Advisory and Ledger SA Tomas Varenholt Director and Founder Certified Accountant Tel. 022 418 57 34 tv@clairevalconseil.ch www.clairevalconseil.ch Rue des Vergières 27 1201 Geneva
Target Market(s)
Our customers are small companies, start-ups and new companies.
Industry/Entity Type
Finance And Accounting
Contact Information for Business Card
Claireval Conseil et Comptes SA
Tomas Varenholt
Directeur et Fondateur
Expert-comptable diplômé
Tél. 022 418 57 34
tv@clairevalconseil.ch
www.clairevalconseil.ch
Rue des Vergières 27
1201 Genève

```html
<!DOCTYPE html>
<html lang="fr">
<head>
<meta charset="utf-8">
<title>Claireval Conseil et Comptes SA – Carte de visite</title>
<link href="https://fonts.googleapis.com/css2?family=Roboto:wght@400;500;700&display=swap" rel="stylesheet">
<style>
  :root {
    --page-bg: #d8d5d0;
    --card-bg: #eeece8;
    --card-edge: #d2cfca;
    --ink: #2b2b2b;
    --ink-soft: #333333;
    --accent: #1d5a8c;
    --mark-blue: #2c86c1;
  }
  * { margin: 0; padding: 0; box-sizing: border-box; }
  html, body {
    width: 1200px;
    height: 1054px;
    overflow: hidden;
    background: var(--page-bg);
    font-family: "Roboto", Arial, sans-serif;
  }
  .card {
    position: absolute;
    left: 100px;
    top: 227px;
    width: 1000px;
    height: 600px;
    background: var(--card-bg);
    border: 1px solid var(--card-edge);
    border-radius: 6px;
    box-shadow: 0 10px 30px rgba(0,0,0,0.12);
    overflow: hidden;
  }
  .brand-mark {
    position: absolute;
    left: 40px;
    top: 90px;
    width: 440px;
    height: 440px;
    background: var(--mark-blue);
    opacity: 0.85;
    border-radius: 10px;
  }
  .brand {
    position: absolute;
    right: 38px;
    top: 48px;
    text-align: right;
    color: var(--ink);
    font-weight: 500;
  }
  .brand-name {
    display: block;
    font-size: 74px;
    line-height: 1;
    letter-spacing: 5px;
    margin-right: -5px;
  }
  .brand-tagline {
    display: block;
    font-size: 27px;
    line-height: 1;
    letter-spacing: 4.5px;
    margin-top: 16px;
    margin-right: -4.5px;
  }
  .person {
    position: absolute;
    right: 38px;
    top: 268px;
    text-align: right;
  }
  .person-name {
    font-size: 34px;
    font-weight: 700;
    color: var(--accent);
    line-height: 1.2;
  }
  .person-role {
    font-size: 22px;
    color: var(--ink-soft);
    line-height: 1.4;
  }
  .person-role:first-of-type { margin-top: 6px; }
  .contact {
    position: absolute;
    right: 38px;
    top: 402px;
    list-style: none;
    text-align: right;
    font-size: 24px;
    color: var(--ink-soft);
  }
  .contact-item {
    display: flex;
    justify-content: flex-end;
    align-items: center;
    gap: 14px;
    height: 38px;
  }
  .contact-icon { width: 22px; height: 22px; fill: var(--accent); }
  .contact-address { margin-top: 10px; }
</style>
</head>
<body>
  <main class="card">
    <div class="brand-mark" role="img" aria-label="Emplacement du symbole de la marque Claireval"></div>

    <div class="brand">
      <span class="brand-name">CLAIREVAL</span>
      <span class="brand-tagline">CONSEIL ET COMPTES</span>
    </div>

    <div class="person">
      <p class="person-name">Tomas Varenholt</p>
      <p class="person-role">Directeur et Fondateur</p>
      <p class="person-role">Expert-comptable diplômé</p>
    </div>

    <ul class="contact">
      <li class="contact-item">
        <span>022 418 57 34</span>
        <svg class="contact-icon" viewBox="0 0 24 24" aria-hidden="true"><path d="M3 8c0-3 4-5 9-5s9 2 9 5v2h-5V8H8v2H3zM6 11h12l2 8H4zM12 13a3 3 0 1 0 0 6 3 3 0 0 0 0-6z"/></svg>
      </li>
      <li class="contact-item">
        <span>tv@clairevalconseil.ch</span>
        <svg class="contact-icon" viewBox="0 0 24 24" aria-hidden="true"><path d="M2 5h20v14H2zM4 7v.5l8 6 8-6V7zM4 10v7h16v-7l-8 6z"/></svg>
      </li>
      <li class="contact-item">
        <span>www.clairevalconseil.ch</span>
        <svg class="contact-icon" viewBox="0 0 24 24" aria-hidden="true"><path d="M12 2a10 10 0 1 0 0 20 10 10 0 0 0 0-20zm0 2c1.2 1.3 2 3.3 2.3 5.5H9.7C10 7.3 10.8 5.3 12 4zM4.3 11h3.4c0 1.1 0 2.1.1 3H4.6a8 8 0 0 1-.3-3zm5.4 0h4.6c0 1.1 0 2.1-.1 3H9.8c-.1-.9-.1-1.9-.1-3zm6.6 0h3.4a8 8 0 0 1-.3 3h-3.2c.1-.9.1-1.9.1-3zM5.3 16h2.8c.3 1.4.8 2.6 1.4 3.6A8 8 0 0 1 5.3 16zm4.9 0h3.6c-.4 1.6-1 2.9-1.8 3.9-.8-1-1.4-2.3-1.8-3.9zm5.7 0h2.8a8 8 0 0 1-4.2 3.6c.6-1 1.1-2.2 1.4-3.6zM4.8 9.5A8 8 0 0 1 9.5 4.4c-.8 1.4-1.4 3.1-1.7 5.1zm11.4 0c-.3-2-.9-3.7-1.700-5.1a8 8 0 0 1 4.7 5.1z"/></svg>
      </li>
      <li class="contact-item contact-address">
        <span>Rue des Vergières 27 1201 Genève</span>
      </li>
    </ul>
  </main>
</body>
</html>
```